Webdesign für neue Weinmarke
Zielgruppe
Kelchwandler ist eine neue Weinmarke. Es wird vorerst drei grundlegende Sorten geben: einen Rotwein, einen Weißwein und einen Rosé. Für diese neue Weinmarke wollen wir eine Webseite gestalten, welche die Weine ansprechend darstellt und zusätzlich den Kunden die Möglichkeit gibt, mehr Informationen über den Wein einzuholen. Die Marke Kelchwandler ist auch im Etikett an den Graf von Tressenbach angelehnt. Das Etikett zeigt den Baron, wie er auf einem Weinfass reitet – daher der Name „Kelchwandler“. Die Story, die wir mit dem Wein spielen, ist, dass die besonderen Fähigkeiten des Barons auch auf den Genuss des Kelchwandler zurückzuführen sind.
Die Zielgruppe für den Kelchwandler ist breit gefächert und schließt per se erst mal keine Personengruppe aus. Der Wein soll eher im niedrigeren Preissegment verkauft werden.
Aufgabenstellung
Es soll eine neue Webseite designt werden, die sich im Aufbau an der die Webseite http://www.velgor-example.de/#!/de/unsere-weine/sortiment orientieren kann. Zudem können für die Entwicklung kleine Animationen berücksichtigt werden, die die Seite auflockern. Das Design soll eine responsive Webseite unterstützen. Das Design soll zur Weinmarke Kelchwandler passen von der wir bisher nur das Etikett haben.

```html
<!DOCTYPE html>
<html lang="de">
<head>
<meta charset="utf-8">
<title>Kelchwandler – Rotwein</title>
<link href="https://fonts.googleapis.com/css2?family=Pathway+Gothic+One&family=Mukta:wght@300;400&display=swap" rel="stylesheet">
<style>
:root{
  --paper:#faf8f5;
  --ink:#2a2426;
  --wine:#3d1e27;
  --wine-deep:#2e151c;
  --white:#ffffff;
  --green:#9fb51f;
  --red:#d2404b;
  --footer:#dcdcdc;
  --head:"Pathway Gothic One", "Arial Narrow", sans-serif;
  --body:"Mukta", "Helvetica Neue", sans-serif;
}
*{margin:0;padding:0;box-sizing:border-box}
html,body{width:1133px;height:1200px;overflow:hidden}
body{background:var(--paper);color:var(--ink);font-family:var(--body);font-weight:300;position:relative}
.abs{position:absolute}

/* header */
.main-nav{left:36px;top:7px;font-family:var(--head);font-size:11px;line-height:14.6px;list-style:none}
.main-nav li{color:var(--ink)}
.nav-marker{left:0;top:25px}
.meta-nav{right:13px;top:8px;font-family:var(--head);font-size:9.5px;line-height:15px;text-align:right;list-style:none;color:var(--ink)}
.brand{left:0;width:1133px;top:96px;text-align:center;font-family:var(--body);font-weight:400;font-size:16px;letter-spacing:1px;color:var(--ink)}

/* hero */
.hero-band{left:0;top:162px}
.hero-heading{left:241px;top:216px;width:290px;color:var(--white);font-family:var(--head);font-weight:400;z-index:2}
.hero-title{font-size:44px;line-height:46px;white-space:nowrap}
.hero-sub{font-size:29px;line-height:32px;white-space:nowrap;margin-top:2px}
.btn{border:1.5px solid var(--white);border-radius:12px;color:var(--white);font-family:var(--body);font-weight:300;display:flex;align-items:center;justify-content:center;gap:7px}
.btn-back{left:823px;top:224px;width:69px;height:22px;font-size:12px}
.btn-order{left:241px;top:533px;width:104px;height:21px;font-size:12px}
.bottle-hero{left:521px;top:198px;z-index:1}

.spec{display:flex;align-items:flex-start;gap:9px;color:var(--white)}
.spec-label{font-family:var(--head);font-size:11px;line-height:12px;display:block}
.spec-value{font-size:12px;line-height:14px;display:block}
.spec-grape{left:243px;top:384px}
.spec-origin{left:369px;top:384px}
.spec-temp{left:250px;top:465px}
.spec-taste{left:364px;top:465px}

.details{left:636px;top:357px;width:257px;color:var(--white);font-size:9.3px;line-height:13px}
.details p{margin-bottom:15px}
.details .lbl{font-family:var(--head);font-size:10px}

/* products */
.divider{left:478px;width:177px;height:2px;background:var(--ink)}
.section-title{left:0;width:1133px;top:731px;text-align:center;font-family:var(--head);font-weight:400;font-size:20px;color:var(--ink)}

.card{top:792px}
.card-text{color:var(--white)}
.card-title{font-family:var(--head);font-size:18px;line-height:20px}
.card-sub{font-family:var(--head);font-size:12.5px;line-height:15px;margin-top:2px}
.card-rule{width:63px;height:1.5px;background:var(--white);margin:6px 0 8px}
.card-body{font-size:9px;line-height:13px;width:225px}
.btn-details{width:71px;height:21px;font-size:12px}

/* footer */
.footer-band{left:0;top:1120px}
.copyright{left:242px;top:1166px;font-size:9.5px;color:var(--ink)}
.legal{right:242px;top:1166px;font-size:9.5px;display:flex;gap:6px;color:var(--ink)}
.legal span+span{border-left:1px solid #b9b4b5;padding-left:6px}
.dot-nav{right:10px;top:1139px;list-style:none;text-align:right}
.dot-nav li{height:18px;display:flex;align-items:center;justify-content:flex-end;gap:5px;font-size:8px;color:var(--white)}
.dot{width:8px;height:8px;border:1.3px solid var(--white);border-radius:50%;display:inline-block}
.dot.active{box-shadow:inset 0 0 0 1.5px var(--footer),inset 0 0 0 4px var(--white)}
</style>
</head>
<body>

<!-- header -->
<svg class="abs nav-marker" width="34" height="8" viewBox="0 0 34 8" aria-hidden="true">
  <line x1="0" y1="4" x2="30" y2="4" stroke="#2a2426" stroke-width="1.2"/>
  <path d="M26 1 L32 4 L26 7 Z" fill="#2a2426"/>
</svg>
<ul class="abs main-nav">
  <li>Willkommen</li>
  <li>Kelchwandler Rotwein</li>
  <li>Kelchwandler Rosé</li>
  <li>Kelchwandler Weißwein</li>
</ul>
<ul class="abs meta-nav">
  <li>Kontakt</li>
  <li>Impressum</li>
</ul>
<div class="abs brand">KELCHWANDLER</div>

<!-- hero band -->
<svg class="abs hero-band" width="1133" height="460" viewBox="0 0 1133 460" aria-hidden="true">
  <defs>
    <radialGradient id="heroTone" cx="0.5" cy="0.45" r="0.7">
      <stop offset="0" stop-color="#47242e"/>
      <stop offset="1" stop-color="#3a1c25"/>
    </radialGradient>
  </defs>
  <path d="M0 12 L480 12 Q540 9 566 5 Q592 9 652 12 L1133 12 L1133 444 L660 444 Q600 446 566 452 Q532 446 472 444 L0 444 Z" fill="url(#heroTone)"/>
</svg>

<div class="abs hero-heading">
  <h1 class="hero-title">Kelchwandler Rotwein</h1>
  <h2 class="hero-sub">Kelchwandler Pfälzer Dornfelder</h2>
</div>

<div class="abs btn btn-back"><span>‹</span><span>Zurück</span></div>

<svg class="abs bottle-hero" width="90" height="386" viewBox="0 0 90 386" role="img" aria-label="Produktfoto: Flasche Dornfelder halbtrocken mit hellem Etikett">
  <defs>
    <linearGradient id="bottleDark" x1="0" x2="1">
      <stop offset="0" stop-color="#1c1013"/>
      <stop offset="0.35" stop-color="#3b2128"/>
      <stop offset="1" stop-color="#140a0d"/>
    </linearGradient>
  </defs>
  <path d="M32 2 H58 V78 Q60 150 84 210 Q88 225 88 240 V376 Q88 384 80 384 H10 Q2 384 2 376 V240 Q2 225 6 210 Q30 150 32 78 Z" fill="url(#bottleDark)"/>
  <rect x="7" y="237" width="76" height="118" fill="#e9e6e6"/>
</svg>

<div class="abs spec spec-grape">
  <svg width="32" height="32" viewBox="0 0 32 32" aria-hidden="true" fill="#fff">
    <circle cx="22" cy="8" r="4"/><circle cx="14" cy="10" r="4"/><circle cx="22" cy="16" r="4"/>
    <circle cx="13" cy="18" r="4"/><circle cx="6" cy="17" r="3.5"/><circle cx="18" cy="24" r="4"/>
    <circle cx="9" cy="25" r="4"/><circle cx="4" cy="29" r="3"/>
    <path d="M24 4 Q28 1 31 2" stroke="#fff" stroke-width="1.5" fill="none"/>
  </svg>
  <div><span class="spec-label">Rebsorte:</span><span class="spec-value">Dornfelder</span></div>
</div>
<div class="abs spec spec-origin">
  <div role="img" aria-label="Landkarte Deutschland" style="width:24px;height:32px;background:#fff;border-radius:9px 7px 10px 6px"></div>
  <div><span class="spec-label">Herkunft:</span><span class="spec-value">Deutschland (Pfalz)</span></div>
</div>
<div class="abs spec spec-temp">
  <svg width="22" height="34" viewBox="0 0 22 34" aria-hidden="true" fill="none" stroke="#fff" stroke-width="1.6">
    <path d="M5 3 Q5 1 8 1 Q11 1 11 3 V22 A7 7 0 1 1 5 22 Z"/>
    <circle cx="8" cy="27" r="3.5" fill="#fff" stroke="none"/>
    <line x1="14" y1="5" x2="19" y2="5"/><line x1="14" y1="10" x2="19" y2="10"/><line x1="14" y1="15" x2="19" y2="15"/>
  </svg>
  <div style="margin-left:3px"><span class="spec-label">Trinktemperatur:</span><span class="spec-value">16-18 °C</span></div>
</div>
<div class="abs spec spec-taste">
  <svg width="36" height="20" viewBox="0 0 36 20" aria-hidden="true" style="margin-top:10px">
    <g fill="#6e4d56"><path d="M2 2h2v4l1.5 3v11h-5V9L2 6z"/><path d="M21 2h2v4l1.5 3v11h-5V9L21 6z"/><path d="M30 2h2v4l1.5 3v11h-5V9L30 6z"/></g>
    <path d="M11 2h2v4l1.5 3v11h-5V9L11 6z" fill="#fff"/>
  </svg>
  <div><span class="spec-label">Geschmack:</span><span class="spec-value">Halbtrocken</span></div>
</div>

<div class="abs btn btn-order"><span>Jetzt bestellen</span><span>›</span></div>

<div class="abs details">
  <p><span class="lbl">Charakteristik:</span> Des Kelchwandlers Pfälzer Dornfelder, ein edler Tropfen, vermag es seinem Genießer wundersame Eindrücke zu verleihen. Rubinrot, fruchtbetont und gehaltvoll ermutigte er bereits den Baron selbst auf einer Kanonenkugel zu reiten und noch in der Luft auf die nächste zu springen.</p>
  <p><span class="lbl">Verzehrempfehlung:</span> Hervorragend herzhaften Fleischgerichten und kräftigen Käsesorten.</p>
  <p><span class="lbl">Region:</span> Des Kelchwandlers Rot- sowie Weißwein kommen aus dem zweitgrößten deutschen Weinanbaugebiet,<br>der Pfalz. Das einzigartige Klima dieser Region bringt gehaltvolle und wertige Weine hervor. Die Pfalz ist Deutschlands größtes Rotweingebiet und beheimatet zudem auch des Kelchwandlers feinherben Riesling.</p>
</div>

<!-- products -->
<div class="abs divider" style="top:681px" role="img" aria-label="Zierlinie"></div>
<h3 class="abs section-title">Weitere Produkte</h3>

<svg class="abs card" style="left:241px" width="304" height="210" viewBox="0 0 304 210" role="img" aria-label="Produktkarte Weißwein mit Flaschenfoto">
  <path d="M44 8 Q80 3 140 6 L303 6 L303 187 L46 187 Q40 190 36 195 Z" fill="var(--green)"/>
  <path d="M20 -12 H33 V30 Q34 70 46 110 Q49 120 49 130 V205 Q49 208 45 208 H5 Q1 208 1 205 V130 Q1 120 4 110 Q18 70 20 30 Z" fill="#b8a64a"/>
  <rect x="20" y="-12" width="13" height="40" fill="#1c1a1a"/>
  <rect x="3" y="137" width="44" height="55" fill="#eceae4"/>
</svg>
<div class="abs card-text" style="left:312px;top:818px">
  <div class="card-title">Kelchwandler Weißwein</div>
  <div class="card-sub">Kelchwandler Pfälzer Riesling</div>
  <div class="card-rule"></div>
  <p class="card-body">Muster Kurze Beschreibung Lorem ipsum dolor sit amet consetetur sadipscing elitr, sed diam nonumy eirmod tempor invidunt vero eos et accusam et justo labore et dolore magna aliquyam erat, sed diam voluptua.</p>
</div>
<div class="abs btn btn-details" style="left:456px;top:937px"><span>Details</span><span>›</span></div>

<svg class="abs card" style="left:588px" width="304" height="210" viewBox="0 0 304 210" role="img" aria-label="Produktkarte Rosé mit Flaschenfoto">
  <path d="M44 8 Q80 3 140 6 L303 6 L303 187 L46 187 Q40 190 36 195 Z" fill="var(--red)"/>
  <path d="M20 -12 H33 V30 Q34 70 46 110 Q49 120 49 130 V205 Q49 208 45 208 H5 Q1 208 1 205 V130 Q1 120 4 110 Q18 70 20 30 Z" fill="#e0324a"/>
  <rect x="20" y="-12" width="13" height="40" fill="#1c1a1a"/>
  <rect x="3" y="137" width="44" height="55" fill="#eee6e8"/>
</svg>
<div class="abs card-text" style="left:659px;top:818px">
  <div class="card-title">Kelchwandler Rosé</div>
  <div class="card-sub">Kelchwandler lieblicher Rosé</div>
  <div class="card-rule"></div>
  <p class="card-body">Muster Kurze Beschreibung Lorem ipsum dolor sit amet consetetur sadipscing elitr, sed diam nonumy eirmod tempor invidunt vero eos et accusam et justo labore et dolore magna aliquyam erat, sed diam voluptua.</p>
</div>
<div class="abs btn btn-details" style="left:803px;top:937px"><span>Details</span><span>›</span></div>

<div class="abs divider" style="top:1066px" role="img" aria-label="Zierlinie"></div>

<!-- footer -->
<svg class="abs footer-band" width="1133" height="80" viewBox="0 0 1133 80" aria-hidden="true">
  <path d="M0 7 L500 7 Q530 5 548 2 Q566 6 584 4 Q610 6 640 7 L1133 7 L1133 80 L0 80 Z" fill="var(--footer)"/>
</svg>
<div class="abs copyright">© Kelchwandler 2018. Alle rechte vorbehalten.</div>
<div class="abs legal"><span>Impressum</span><span>Datenschutz</span></div>
<ul class="abs dot-nav">
  <li>Kelchwandler Rotwein <span class="dot active"></span></li>
  <li><span class="dot"></span></li>
  <li><span class="dot"></span></li>
</ul>

</body>
</html>
```